New Business Card Design for Manufacturing

We are an engineering/manufacturing company that offers Advanced machining/assembly/engineering services, as well as innovative products for the heavy duty engine cooling markets.

We are looking to get a new business card designed that is clean and modern looking, but still fits the wide range of technical/skilled work we do.

- We hope to use this design as the base for other design work in new Presentations, web, and print work.

Industry/Entity Type

Engineering

Contact Information for Business Card

Our preferred color of blue is (RGB) 22/71/159 but can vary slightly from that color. Our content will be our Logo and full company name (Vantrell Forge Works, Inc.), company address, name, job title, phone number with extension, cell number, fax number, website, and email address on the cards.
We'd like the full company name next to the logo, but we are open to other interpretations of that layout.
Preferably, we would like the back side to be clean with just our logo, and the front to contain all of the contact information.

Colors
2f74b4
0355a3
85abd2

Requirements
Must have
• - Logo, company name, needed content - We are open to interpretation beyond that.
• - Standard size business card.
• - Horizontal orientation.
• - Enough space for lengthy names / job titles (for example, a job title could read "Directory of Human Resources" or "V.P. of Governmental Affairs"). We need this to look clean, whether the title be short (CEO) or long (as described above).

```html
<!DOCTYPE html>
<html lang="en">
<head>
<meta charset="utf-8">
<title>Vantrell Forge Works – Business Card</title>
<link rel="stylesheet" href="https://fonts.googleapis.com/css2?family=Open+Sans:wght@400;700;800&family=Source+Serif+4:wght@400;600&display=swap">
<style>
  :root {
    --brand-blue: #16479f;
    --deep-blue: #0b2f6e;
    --bright-blue: #0355a3;
    --ink: #3a3f44;
    --steel: #848d94;
    --paper: #ffffff;
    --backdrop: #e4e5e8;
  }
  * { box-sizing: border-box; margin: 0; padding: 0; }
  html, body { width: 1200px; height: 1200px; overflow: hidden; }
  body {
    background: var(--backdrop);
    display: flex; flex-direction: column; align-items: center; justify-content: center; gap: 60px;
    font-family: "Open Sans", sans-serif;
  }
  .card {
    position: relative; width: 840px; height: 480px; overflow: hidden;
    box-shadow: 0 10px 30px rgba(0,0,0,.12);
  }
  .card-front { background: var(--paper); }
  .card-back {
    background: radial-gradient(circle at 52% 48%, #0a55b0 0%, #0a3f8a 45%, var(--deep-blue) 100%);
    display: flex; align-items: center; justify-content: center;
  }
  .bands { position: absolute; left: 0; bottom: 0; width: 840px; height: 160px; }
  .holder { position: absolute; left: 60px; top: 58px; }
  .holder-name {
    font-family: "Source Serif 4", serif; font-weight: 400; font-size: 36px; color: var(--brand-blue); line-height: 1.1;
  }
  .holder-role { display: flex; align-items: center; gap: 8px; margin-top: 6px; font-size: 16px; color: var(--ink); }
  .company-name {
    position: absolute; left: 60px; top: 150px;
    font-family: "Source Serif 4", serif; font-size: 18px; letter-spacing: .06em; text-transform: uppercase; color: var(--brand-blue);
  }
  .rule { position: absolute; left: 60px; top: 186px; width: 720px; height: 1px; background: var(--bright-blue); opacity: .7; }
  .contacts { position: absolute; left: 60px; top: 206px; display: flex; }
  .contact-col { padding: 0 22px; border-left: 1px solid #8fb0d6; display: flex; flex-direction: column; gap: 8px; }
  .contact-col:first-child { padding-left: 0; border-left: 0; }
  .contact-line { display: flex; align-items: center; gap: 8px; font-size: 15px; color: var(--ink); white-space: nowrap; }
  .contact-line .ext { color: var(--brand-blue); }
  .icon { width: 18px; height: 18px; flex: none; }
  .mark { position: absolute; right: 56px; top: 58px; display: flex; align-items: center; gap: 12px; }
  .mark-square { width: 18px; height: 18px; background: var(--brand-blue); }
  .mark-name { font-weight: 800; font-size: 22px; line-height: 1.1; color: var(--brand-blue); text-transform: uppercase; letter-spacing: .02em; }
  .back-name { font-weight: 800; font-size: 46px; color: #0a3a80; text-transform: uppercase; letter-spacing: .03em; }
</style>
</head>
<body>
  <section class="card card-front" aria-label="Business card front">
    <div class="mark">
      <span class="mark-square"></span>
      <span class="mark-name">Vantrell<br>Forge Works</span>
    </div>

    <div class="holder">
      <p class="holder-name">Daniel Hartwell</p>
      <p class="holder-role">Director |
        <svg class="icon" viewBox="0 0 18 18"><rect width="18" height="18" rx="4" fill="var(--brand-blue)"/><rect x="6" y="3.5" width="6" height="11" rx="1.2" fill="none" stroke="#fff" stroke-width="1.4"/><circle cx="9" cy="12.3" r=".8" fill="#fff"/></svg>
        1 - 555 014288</p>
    </div>

    <p class="company-name">Vantrell Forge Works, Inc.</p>
    <div class="rule"></div>

    <div class="contacts">
      <div class="contact-col">
        <p class="contact-line">
          <svg class="icon" viewBox="0 0 18 18"><rect width="18" height="18" rx="4" fill="var(--brand-blue)"/><path d="M5 4.5c1 0 1.6 1.6 1.6 2.2 0 .6-.9.8-.7 1.4.4 1 1.2 1.8 2.2 2.3.6.2.8-.7 1.4-.7.6 0 2.2.6 2.2 1.6 0 .8-1 1.7-2 1.7C6.8 13 4 10.2 4 7c0-1 .3-2.5 1-2.5z" fill="#fff"/></svg>
          1 - 555 019374</p>
        <p class="contact-line">
          <svg class="icon" viewBox="0 0 18 18"><rect width="18" height="18" rx="4" fill="var(--brand-blue)"/><rect x="3.5" y="5.5" width="11" height="7.5" rx="1" fill="#fff"/><path d="M3.8 6l5.2 4 5.2-4" fill="none" stroke="var(--brand-blue)" stroke-width="1.2"/></svg>
          daniel@vantrellforge.com</p>
      </div>
      <div class="contact-col">
        <p class="contact-line">
          <svg class="icon" viewBox="0 0 18 18"><rect width="18" height="18" rx="4" fill="var(--brand-blue)"/><path d="M5 4.5c1 0 1.6 1.6 1.6 2.2 0 .6-.9.8-.7 1.4.4 1 1.2 1.8 2.2 2.3.6.2.8-.7 1.4-.7.6 0 2.2.6 2.2 1.6 0 .8-1 1.7-2 1.7C6.8 13 4 10.2 4 7c0-1 .3-2.5 1-2.5z" fill="#fff"/></svg>
          1 - 555 014288 <span class="ext">(ext)</span></p>
        <p class="contact-line">
          <svg class="icon" viewBox="0 0 18 18"><rect width="18" height="18" rx="4" fill="var(--brand-blue)"/><circle cx="9" cy="9" r="5" fill="none" stroke="#fff" stroke-width="1.2"/><ellipse cx="9" cy="9" rx="2.2" ry="5" fill="none" stroke="#fff" stroke-width="1"/><path d="M4 9h10" stroke="#fff" stroke-width="1"/></svg>
          www.vantrellforge.com</p>
      </div>
      <div class="contact-col">
        <p class="contact-line">
          <svg class="icon" viewBox="0 0 18 18"><rect width="18" height="18" rx="4" fill="var(--brand-blue)"/><path d="M9 3.5a3.8 3.8 0 0 1 3.8 3.8c0 2.8-3.8 7.2-3.8 7.2S5.2 10.1 5.2 7.3A3.8 3.8 0 0 1 9 3.5z" fill="#fff"/><circle cx="9" cy="7.3" r="1.4" fill="var(--brand-blue)"/></svg>
          Dummy city</p>
        <p class="contact-line">Dummy Country Land</p>
      </div>
    </div>

    <svg class="bands" viewBox="0 0 840 160" preserveAspectRatio="none" aria-hidden="true">
      <path d="M0 24 H440 Q462 24 476 40 L480 44 H0 Z" fill="var(--brand-blue)"/>
      <path d="M0 44 H470 Q486 44 496 36 Q506 28 522 28 H840 V160 H0 Z" fill="var(--steel)"/>
    </svg>
  </section>

  <section class="card card-back" aria-label="Business card back">
    <p class="back-name">Vantrell Forge Works</p>
  </section>
</body>
</html>
```